Buch-/E-Book-Cover im Bereich der Persönlichkeitsentwicklung
Vielen lieben Dank für die super Arbeit von Dir. Das Design ist klasse und die vielen Vorschläge waren auch super. Die komplette Zusammenarbeit verlief sehr professionell und Änderungswünsche wurden sehr schnell umgesetzt. Ich kann Dich voll und ganz weiterempfehlen.
Zielgruppe
Wir arbeiten in der Persönlichkeitsentwicklung für Jugendliche. Dabei spezialisieren wir uns auf den Altersbereich 12 - 17 Jahre. Unser Ziel ist es jungen Menschen zu zeigen, wie Sie zu sich selbst finden und ein glückliches sowie erfolgreiches Leben führen können.
Aufgabenstellung
- Das Design sollte für die Eltern von Teenagern und auch für die Teenager selbst ausgelegt werden. Das Buch ist für die Jugendlichen (Mädchen und Jungen im Alter zwischen 12 Jahren und 17 Jahren) gedacht, wird allerdings meist von deren Mütter gekauft.
- Der Name des Autors lautet: Henrik Falbe
- Der Titel lautet: Junge Herzen finden Mut und Richtung
- Der Untertitel lautet: Was Heranwachsende über ihren Weg lernen
- Im Anhang befinden sich Designs, die ich gut finde (nur falls jemand weitere Ideen haben möchte)
- Format: 15,24 cm x 22,86 cm (6' x 9') [genaue Maße fürs Taschenbuch und Hardcover sind im Anhang (.zip Dateien)]
1. E-Book:
- Coverdateien sollten idealerweise 2 560 Pixel hoch und 1 600 Pixel breit sein. Zur Gewährleistung der bestmöglichen Qualität (insbesondere auf HD-Geräten) sollte das Bild mindestens 2 500 Pixel hoch sein.
- Format: TIFF (.tif/.tiff) oder JPEG (.jpeg/.jpg)
- DPI: 72 dpi
- Größe: Ihr Coverbild muss kleiner als 50 MB sein.
Hinweis: Vermeiden Sie es, Ihre Dateien zu komprimieren. Dies kann die Qualität Ihres Covers auf Lesegeräten beeinträchtigen. Das beste Ergebnis erzielen Sie mit Bildern, die eine Mindestauflösung von 300 ppi (Pixels per Inch) haben.
- Rahmen: Coverbilder mit weißem oder sehr hellem Hintergrund heben sich kaum vom weißen Hintergrund ab. Fügen Sie einen dünnen Rahmen (3–4 Pixel) in Mittelgrau hinzu, um die Ränder des Covers besser sichtbar zu machen.
2. + 3. Taschenbuch/Hardcover [genaue Maße fürs Taschenbuch und Hardcover sind im Anhang (.zip Dateien)] :
- Dateityp: Das Cover muss als einzelne PDF-Datei vorliegen und die hintere Coverseite, den Buchrücken und die vordere Coverseite als einzelnes Bild enthalten.
- Dateigröße: Coverdateien, die größer als 650 MB sind, können nicht konvertiert werden. Die Datei sollte maximal 40 MB groß sein, da sich bei großen Dateien der Druck verlangsamt.
- Die gen..

```html
<!DOCTYPE html>
<html lang="de">
<head>
<meta charset="utf-8">
<title>Junge Herzen finden Mut und Richtung – Coverentwurf</title>
<link rel="stylesheet" href="https://fonts.googleapis.com/css2?family=Rubik+Dirt&family=Oswald:wght@300;500&family=Pathway+Gothic+One&display=swap">
<style>
  :root {
    --page: #ffffff;
    --cyan: #14aec8;
    --teal: #2a93a3;
    --slate: #4b6e80;
    --pine: #466f73;
    --ocean: #1a87bd;
    --graphite: #566a73;
    --ink: #141414;
    --white: #ffffff;
    --cape: #e2202a;
    --book: #e9ebef;
  }
  * { box-sizing: border-box; margin: 0; padding: 0; }
  html, body { width: 1200px; height: 800px; overflow: hidden; background: var(--page); }
  .canvas { position: relative; width: 1200px; height: 800px; }

  .cover {
    position: absolute; width: 483px; height: 724px;
    background: var(--bg, var(--cyan)); overflow: hidden; color: var(--white);
  }
  .cover--main { left: 28px; top: 40px; }

  .thumb { position: absolute; width: 152px; height: 228px; overflow: hidden; }
  .thumb .cover { transform: scale(0.3147); transform-origin: 0 0; left: 0; top: 0; }

  .author {
    position: absolute; top: 26px; left: 0; width: 100%; text-align: center;
    font-family: "Oswald", sans-serif; font-weight: 500; font-size: 21px; letter-spacing: 1px;
    text-transform: uppercase;
  }
  .title { position: absolute; inset: 0; }
  .title span { position: absolute; white-space: nowrap; line-height: 1; }
  .title .strong { font-family: "Rubik Dirt", sans-serif; color: var(--white); }
  .title .soft { font-family: "Oswald", sans-serif; font-weight: 300; color: var(--ink); }
  .title .w1 { left: 62px; top: 104px; font-size: 52px; transform: rotate(-3deg); }
  .title .w2 { left: 148px; top: 160px; font-size: 44px; transform: rotate(-3deg); }
  .title .w3 { left: 36px; top: 206px; font-size: 124px; transform: rotate(-2deg); }
  .title .w4 { left: 36px; top: 348px; font-size: 40px; }
  .title .w5 { left: 112px; top: 338px; font-size: 66px; transform: rotate(-1deg); }

  .subtitle {
    position: absolute; left: 268px; top: 458px;
    font-family: "Pathway Gothic One", sans-serif; font-size: 31px; line-height: 1.06;
    text-transform: uppercase; color: var(--white);
  }
  .decor { position: absolute; left: 0; top: 0; }
  .hero-art {
    position: absolute; left: 160px; top: 478px; width: 112px; height: 246px;
    background: linear-gradient(180deg, rgba(255,255,255,0.0) 0%, rgba(226,32,42,0.55) 35%, rgba(20,20,20,0.55) 62%, rgba(233,235,239,0.85) 80%);
  }
</style>
</head>
<body>
<main class="canvas">

  <article class="cover cover--main" style="--bg: var(--cyan)">
    <p class="author">Henrik Falbe</p>
    <h1 class="title">
      <span class="strong w1">Junge Herzen</span>
      <span class="soft w2">finden</span>
      <span class="strong w3">Mut</span>
      <span class="soft w4">und</span>
      <span class="strong w5">Richtung</span>
    </h1>
    <svg class="decor" width="483" height="724" viewBox="0 0 483 724" aria-hidden="true">
      <polygon fill="#fff" points="220,437 224,448 236,449 227,456 230,467 220,461 210,467 213,456 204,449 216,448"/>
      <g fill="#fff">
        <path d="M128 480 a8 8 0 0 1 12 -8 a11 11 0 0 1 20 6 a6 6 0 0 1 0 12 h-30 a6 6 0 0 1 -2 -10z"/>
        <path d="M60 619 a8 8 0 0 1 12 -8 a11 11 0 0 1 20 6 a6 6 0 0 1 0 12 h-30 a6 6 0 0 1 -2 -10z"/>
        <path d="M300 599 a8 8 0 0 1 12 -8 a11 11 0 0 1 20 6 a6 6 0 0 1 0 12 h-30 a6 6 0 0 1 -2 -10z"/>
        <path d="M340 692 a10 10 0 0 1 14 -10 a14 14 0 0 1 26 8 a8 8 0 0 1 0 16 h-38 a7 7 0 0 1 -2 -14z"/>
      </g>
    </svg>
    <div class="hero-art" role="img" aria-label="Illustration: Jugendliche mit rotem Umhang steigt auf einen Bücherstapel und greift nach einem Stern"></div>
    <p class="subtitle">Was Heranwachsende<br>über ihren Weg<br>lernen</p>
  </article>

  <div class="thumb" style="left:546px; top:41px">
    <article class="cover" style="--bg: var(--cyan)">
      <p class="author">Henrik Falbe</p>
      <h2 class="title"><span class="strong w1">Junge Herzen</span><span class="soft w2">finden</span><span class="strong w3">Mut</span><span class="soft w4">und</span><span class="strong w5">Richtung</span></h2>
      <svg class="decor" width="483" height="724" viewBox="0 0 483 724" aria-hidden="true"><polygon fill="#fff" points="220,437 224,448 236,449 227,456 230,467 220,461 210,467 213,456 204,449 216,448"/><g fill="#fff"><path d="M128 480 a8 8 0 0 1 12 -8 a11 11 0 0 1 20 6 a6 6 0 0 1 0 12 h-30 a6 6 0 0 1 -2 -10z"/><path d="M60 619 a8 8 0 0 1 12 -8 a11 11 0 0 1 20 6 a6 6 0 0 1 0 12 h-30 a6 6 0 0 1 -2 -10z"/><path d="M300 599 a8 8 0 0 1 12 -8 a11 11 0 0 1 20 6 a6 6 0 0 1 0 12 h-30 a6 6 0 0 1 -2 -10z"/><path d="M340 692 a10 10 0 0 1 14 -10 a14 14 0 0 1 26 8 a8 8 0 0 1 0 16 h-38 a7 7 0 0 1 -2 -14z"/></g></svg>
      <div class="hero-art" role="img" aria-label="Illustration: Jugendliche auf Bücherstapel"></div>
      <p class="subtitle">Was Heranwachsende<br>über ihren Weg<br>lernen</p>
    </article>
  </div>

  <div class="thumb" style="left:704px; top:41px">
    <article class="cover" style="--bg: var(--teal)">
      <p class="author">Henrik Falbe</p>
      <h2 class="title"><span class="strong w1">Junge Herzen</span><span class="soft w2">finden</span><span class="strong w3">Mut</span><span class="soft w4">und</span><span class="strong w5">Richtung</span></h2>
      <svg class="decor" width="483" height="724" viewBox="0 0 483 724" aria-hidden="true"><polygon fill="#fff" points="220,437 224,448 236,449 227,456 230,467 220,461 210,467 213,456 204,449 216,448"/><g fill="#fff"><path d="M128 480 a8 8 0 0 1 12 -8 a11 11 0 0 1 20 6 a6 6 0 0 1 0 12 h-30 a6 6 0 0 1 -2 -10z"/><path d="M60 619 a8 8 0 0 1 12 -8 a11 11 0 0 1 20 6 a6 6 0 0 1 0 12 h-30 a6 6 0 0 1 -2 -10z"/><path d="M300 599 a8 8 0 0 1 12 -8 a11 11 0 0 1 20 6 a6 6 0 0 1 0 12 h-30 a6 6 0 0 1 -2 -10z"/><path d="M340 692 a10 10 0 0 1 14 -10 a14 14 0 0 1 26 8 a8 8 0 0 1 0 16 h-38 a7 7 0 0 1 -2 -14z"/></g></svg>
      <div class="hero-art" role="img" aria-label="Illustration: Jugendliche auf Bücherstapel"></div>
      <p class="subtitle">Was Heranwachsende<br>über ihren Weg<br>lernen</p>
    </article>
  </div>

  <div class="thumb" style="left:862px; top:41px">
    <article class="cover" style="--bg: var(--slate)">
      <p class="author">Henrik Falbe</p>
      <h2 class="title"><span class="strong w1">Junge Herzen</span><span class="soft w2">finden</span><span class="strong w3">Mut</span><span class="soft w4">und</span><span class="strong w5">Richtung</span></h2>
      <svg class="decor" width="483" height="724" viewBox="0 0 483 724" aria-hidden="true"><polygon fill="#fff" points="220,437 224,448 236,449 227,456 230,467 220,461 210,467 213,456 204,449 216,448"/><g fill="#fff"><path d="M128 480 a8 8 0 0 1 12 -8 a11 11 0 0 1 20 6 a6 6 0 0 1 0 12 h-30 a6 6 0 0 1 -2 -10z"/><path d="M60 619 a8 8 0 0 1 12 -8 a11 11 0 0 1 20 6 a6 6 0 0 1 0 12 h-30 a6 6 0 0 1 -2 -10z"/><path d="M300 599 a8 8 0 0 1 12 -8 a11 11 0 0 1 20 6 a6 6 0 0 1 0 12 h-30 a6 6 0 0 1 -2 -10z"/><path d="M340 692 a10 10 0 0 1 14 -10 a14 14 0 0 1 26 8 a8 8 0 0 1 0 16 h-38 a7 7 0 0 1 -2 -14z"/></g></svg>
      <div class="hero-art" role="img" aria-label="Illustration: Jugendliche auf Bücherstapel"></div>
      <p class="subtitle">Was Heranwachsende<br>über ihren Weg<br>lernen</p>
    </article>
  </div>

  <div class="thumb" style="left:1021px; top:41px">
    <article class="cover" style="--bg: var(--pine)">
      <p class="author">Henrik Falbe</p>
      <h2 class="title"><span class="strong w1">Junge Herzen</span><span class="soft w2">finden</span><span class="strong w3">Mut</span><span class="soft w4">und</span><span class="strong w5">Richtung</span></h2>
      <svg class="decor" width="483" height="724" viewBox="0 0 483 724" aria-hidden="true"><polygon fill="#fff" points="220,437 224,448 236,449 227,456 230,467 220,461 210,467 213,456 204,449 216,448"/><g fill="#fff"><path d="M128 480 a8 8 0 0 1 12 -8 a11 11 0 0 1 20 6 a6 6 0 0 1 0 12 h-30 a6 6 0 0 1 -2 -10z"/><path d="M60 619 a8 8 0 0 1 12 -8 a11 11 0 0 1 20 6 a6 6 0 0 1 0 12 h-30 a6 6 0 0 1 -2 -10z"/><path d="M300 599 a8 8 0 0 1 12 -8 a11 11 0 0 1 20 6 a6 6 0 0 1 0 12 h-30 a6 6 0 0 1 -2 -10z"/><path d="M340 692 a10 10 0 0 1 14 -10 a14 14 0 0 1 26 8 a8 8 0 0 1 0 16 h-38 a7 7 0 0 1 -2 -14z"/></g></svg>
      <div class="hero-art" role="img" aria-label="Illustration: Jugendliche auf Bücherstapel"></div>
      <p class="subtitle">Was Heranwachsende<br>über ihren Weg<br>lernen</p>
    </article>
  </div>

  <div class="thumb" style="left:546px; top:282px">
    <article class="cover" style="--bg: var(--ocean)">
      <p class="author">Henrik Falbe</p>
      <h2 class="title"><span class="strong w1">Junge Herzen</span><span class="soft w2">finden</span><span class="strong w3">Mut</span><span class="soft w4">und</span><span class="strong w5">Richtung</span></h2>
      <svg class="decor" width="483" height="724" viewBox="0 0 483 724" aria-hidden="true"><polygon fill="#fff" points="220,437 224,448 236,449 227,456 230,467 220,461 210,467 213,456 204,449 216,448"/><g fill="#fff"><path d="M128 480 a8 8 0 0 1 12 -8 a11 11 0 0 1 20 6 a6 6 0 0 1 0 12 h-30 a6 6 0 0 1 -2 -10z"/><path d="M60 619 a8 8 0 0 1 12 -8 a11 11 0 0 1 20 6 a6 6 0 0 1 0 12 h-30 a6 6 0 0 1 -2 -10z"/><path d="M300 599 a8 8 0 0 1 12 -8 a11 11 0 0 1 20 6 a6 6 0 0 1 0 12 h-30 a6 6 0 0 1 -2 -10z"/><path d="M340 692 a10 10 0 0 1 14 -10 a14 14 0 0 1 26 8 a8 8 0 0 1 0 16 h-38 a7 7 0 0 1 -2 -14z"/></g></svg>
      <div class="hero-art" role="img" aria-label="Illustration: Jugendliche auf Bücherstapel"></div>
      <p class="subtitle">Was Heranwachsende<br>über ihren Weg<br>lernen</p>
    </article>
  </div>

  <div class="thumb" style="left:704px; top:282px">
    <article class="cover" style="--bg: var(--graphite)">
      <p class="author">Henrik Falbe</p>
      <h2 class="title"><span class="strong w1">Junge Herzen</span><span class="soft w2">finden</span><span class="strong w3">Mut</span><span class="soft w4">und</span><span class="strong w5">Richtung</span></h2>
      <svg class="decor" width="483" height="724" viewBox="0 0 483 724" aria-hidden="true"><polygon fill="#fff" points="220,437 224,448 236,449 227,456 230,467 220,461 210,467 213,456 204,449 216,448"/><g fill="#fff"><path d="M128 480 a8 8 0 0 1 12 -8 a11 11 0 0 1 20 6 a6 6 0 0 1 0 12 h-30 a6 6 0 0 1 -2 -10z"/><path d="M60 619 a8 8 0 0 1 12 -8 a11 11 0 0 1 20 6 a6 6 0 0 1 0 12 h-30 a6 6 0 0 1 -2 -10z"/><path d="M300 599 a8 8 0 0 1 12 -8 a11 11 0 0 1 20 6 a6 6 0 0 1 0 12 h-30 a6 6 0 0 1 -2 -10z"/><path d="M340 692 a10 10 0 0 1 14 -10 a14 14 0 0 1 26 8 a8 8 0 0 1 0 16 h-38 a7 7 0 0 1 -2 -14z"/></g></svg>
      <div class="hero-art" role="img" aria-label="Illustration: Jugendliche auf Bücherstapel"></div>
      <p class="subtitle">Was Heranwachsende<br>über ihren Weg<br>lernen</p>
    </article>
  </div>

</main>
</body>
</html>
```